Business Card Design for Occupational Medicine Start Up Company

We need to design a professional business card. We are a healthcare company providing occupational medicine services to blue collar industries. We are professional, efficient and high quality service providers.

Target Market(s)

Blue Collar Industry: Shipbuilding, Ports, Trucking Companies; The Executives and Safety Officers for these companies

Industry/Entity Type

Healthcare

Contact Information for Business Card

Logo, Name, Title, Email, Phone

Other font styles liked:
• Please match our Brand Guide

Requirements
Must have
• Our Company Colors and Logo

```html
<!DOCTYPE html>
<html lang="en">
<head>
<meta charset="UTF-8">
<title>Crewline Clinics — Business Card</title>
<link href="https://fonts.googleapis.com/css2?family=Montserrat:wght@400;700&display=swap" rel="stylesheet">
<style>
  :root {
    --backdrop: #b4b4b4;
    --card: #363636;
    --ink: #ffffff;
    --ink-soft: #e6e6e6;
    --mark-grey: #9a9a9a;
  }
  * { box-sizing: border-box; margin: 0; padding: 0; }
  html, body {
    width: 1200px;
    height: 846px;
    overflow: hidden;
    background: var(--backdrop);
    font-family: "Montserrat", Arial, sans-serif;
  }
  .sheet {
    width: 1200px;
    height: 846px;
    display: flex;
    align-items: center;
    justify-content: center;
    gap: 40px;
  }
  .card {
    width: 520px;
    height: 297px;
    background: var(--card);
    border-radius: 26px;
    color: var(--ink);
    position: relative;
  }

  /* Contact side */
  .card--contact {
    display: flex;
    align-items: center;
    padding: 0 40px 0 44px;
  }
  .brand-block {
    width: 170px;
    display: flex;
    align-items: center;
    gap: 10px;
  }
  .brand-dot {
    width: 18px;
    height: 18px;
    border-radius: 50%;
    background: var(--mark-grey);
    flex: none;
  }
  .brand-name {
    font-weight: 700;
    font-size: 20px;
    letter-spacing: 0.5px;
    text-transform: uppercase;
  }
  .details { margin-left: 40px; }
  .person-name {
    font-weight: 700;
    font-size: 17px;
    letter-spacing: 0.8px;
  }
  .person-title {
    font-weight: 700;
    font-size: 11px;
    margin: 2px 0 0 10px;
  }
  .contact-list {
    list-style: none;
    margin-top: 20px;
  }
  .contact-list li {
    display: flex;
    align-items: center;
    gap: 10px;
    font-size: 11.5px;
    font-weight: 400;
    color: var(--ink-soft);
    margin-bottom: 7px;
  }
  .contact-icon { width: 14px; height: 14px; flex: none; }

  /* Brand side */
  .card--brand {
    display: flex;
    flex-direction: column;
    align-items: center;
    justify-content: center;
  }
  .brand-wordmark {
    font-weight: 700;
    font-size: 36px;
    letter-spacing: 1px;
    text-transform: uppercase;
  }
  .brand-sub {
    font-weight: 700;
    font-size: 17px;
    letter-spacing: 8px;
    margin-top: 4px;
    text-transform: uppercase;
  }
</style>
</head>
<body>
  <main class="sheet">
    <section class="card card--contact">
      <div class="brand-block">
        <span class="brand-dot"></span>
        <span class="brand-name">Crewline</span>
      </div>
      <div class="details">
        <p class="person-name">FULL NAME</p>
        <p class="person-title">Title</p>
        <ul class="contact-list">
          <li>
            <svg class="contact-icon" viewBox="0 0 24 24" aria-hidden="true"><path fill="#fff" d="M6.6 10.8a15 15 0 0 0 6.6 6.6l2.2-2.2a1 1 0 0 1 1-.25 11.4 11.4 0 0 0 3.6.57 1 1 0 0 1 1 1V20a1 1 0 0 1-1 1A17 17 0 0 1 3 4a1 1 0 0 1 1-1h3.5a1 1 0 0 1 1 1c0 1.25.2 2.45.57 3.57a1 1 0 0 1-.25 1z"/></svg>
            123-456-7890
          </li>
          <li>
            <svg class="contact-icon" viewBox="0 0 24 24" aria-hidden="true"><rect x="2" y="5" width="20" height="14" rx="1" fill="#fff"/><path d="M2.5 6 12 13l9.5-7" stroke="#363636" stroke-width="1.6" fill="none"/></svg>
            full.name@crewlineclinics.com
          </li>
          <li>
            <svg class="contact-icon" viewBox="0 0 24 24" aria-hidden="true"><circle cx="12" cy="12" r="10" fill="#fff"/><g stroke="#363636" stroke-width="1.2" fill="none"><ellipse cx="12" cy="12" rx="4.5" ry="10"/><path d="M2 12h20M4 7h16M4 17h16"/></g></svg>
            CREWLINECLINICS.COM
          </li>
        </ul>
      </div>
    </section>

    <section class="card card--brand">
      <p class="brand-wordmark">Crewline</p>
      <p class="brand-sub">Clinics</p>
    </section>
  </main>
</body>
</html>
```